Wordpress design for media production company

We are a small production company called Copper Lantern Films specializing in documentary and short film.

We are after a wordpress web site that is fun and engaging with a relaxed feel. We would like to be able to easily edit and maintain the website ourselves.

We would like:
* A title screen that has a photo taking up most of the screen.
* Contact details (inc. social media links) on a static bar at the bottom.
* An area for our previous work. Some thumbnails or icons that open up and embedded youtube or vimeo video.
* An area for "about us" which will have information on the company and links to separate profiles of 3 (initially) employees.
* A Blog.
* Somewhere to show what we are currently working on.
* Examples of other stuff we have done (ie. photography, poetry, audio, animation and VFX).

We already have a logo that can be animated. It would be very cool to have it as a "Loading" page while things load in the background.

The text needs to be fun but easy to read.

We already have a license for "Q Layout" which seems pretty cool and flexible, so if you wanted to use it then great but if not then that is fine too.

A couple of pages that we like are:
http://www.plumorchardworks.com/
http://dorianvelkot.com/
http://www.spinthegrove.com/

Please do not hesitate to contact me if you would like more information on anything.

Cheers

Gideon

Target Market(s)

Mainly Australian clients seeking media services
Broadcasting companies

Industry/Entity Type

It Company

Requirements
Nice to have
• I love the parallax look on http://www.plumorchardworks.com/

```html
<!DOCTYPE html>
<html lang="en">
<head>
<meta charset="utf-8">
<title>Copper Lantern Films</title>
<link href="https://fonts.googleapis.com/css2?family=Open+Sans:wght@400;600;700&display=swap" rel="stylesheet">
<style>
:root{
  --red:#c4161c;
  --red-dark:#a50f14;
  --black:#050505;
  --ink:#222;
  --text:#666;
  --muted:#999;
  --light:#f2f2f2;
  --rule:#bbb;
  --white:#fff;
}
*{box-sizing:border-box;margin:0;padding:0}
html,body{width:1200px;height:4700px;overflow:hidden}
body{font-family:"Open Sans",Arial,sans-serif;color:var(--text);background:var(--white);position:relative}
.section{position:absolute;left:0;width:1200px}
.title{position:absolute;left:78px;width:1044px;text-align:center;color:var(--red);font-size:38px;font-weight:400;letter-spacing:1px}
.title-rule{position:absolute;left:78px;width:1044px;border-top:2px dashed var(--rule)}
.intro{position:absolute;left:150px;width:900px;text-align:center;font-size:15px;line-height:26px;color:var(--text)}
.ph{position:absolute}

/* header */
.site-header{top:0;height:204px;background:var(--black)}
.brand{position:absolute;left:70px;top:24px;width:180px;text-align:center}
.brand-mark{width:96px;height:96px;border-radius:50%;background:var(--white);margin:0 auto 10px}
.brand-name{color:var(--white);font-weight:700;font-size:17px;white-space:nowrap}
.search{position:absolute;left:796px;top:44px;width:326px;height:42px;border-radius:21px;background:var(--white);padding:0 18px;font-size:14px;line-height:42px;color:#aaa}
.search svg{position:absolute;right:14px;top:11px}
.main-nav{position:absolute;right:78px;top:120px;display:flex;gap:4px}
.main-nav span{color:var(--white);font-size:15px;font-weight:600;padding:0 14px;height:48px;line-height:48px}
.main-nav .active{background:var(--red)}

/* hero */
.hero{top:204px;height:616px}
.hero-photo{left:0;top:0;width:1200px;height:616px;background:linear-gradient(90deg,#6e6e6e 0%,#9a9a9a 35%,#d8d8d8 60%,#bdbdbd 78%,#8a8a8a 100%)}
.hero-kicker{position:absolute;left:78px;top:164px;color:var(--white);font-size:18px;letter-spacing:1px}
.hero-title{position:absolute;left:78px;top:192px;color:var(--white);font-size:50px;font-weight:700;line-height:62px}
.hero-text{position:absolute;left:78px;top:324px;width:440px;color:#eee;font-size:13px;line-height:20px}
.btn{position:absolute;background:var(--red);color:var(--white);font-size:13px;font-weight:600;text-align:center}
.hero-btn{left:78px;top:426px;width:188px;height:46px;line-height:46px}
.dots{position:absolute;display:flex;gap:8px}
.dots i{width:12px;height:12px;border-radius:50%;border:2px solid var(--white);display:block}
.dots i.on{background:var(--white)}

/* about */
.about{top:820px;height:605px;background:var(--light)}
.member{position:absolute;top:330px;width:182px;height:213px}
.member-photo{position:absolute;left:0;top:0;width:182px;height:175px;background:linear-gradient(180deg,#9a7a68,#3b2c26)}
.member-name{position:absolute;left:0;top:145px;width:182px;height:30px;background:rgba(0,0,0,.55);color:var(--white);font-size:11px;line-height:30px;padding-left:10px}
.member .btn{left:0;top:175px;width:182px;height:38px;line-height:38px;font-size:12px}

/* portfolio */
.portfolio{top:1425px;height:1020px}
.video{left:78px;top:273px;width:1044px;height:486px;background:radial-gradient(circle at 50% 45%,#3a3a3a,#0c0c0c 70%)}
.play{position:absolute;left:565px;top:498px;width:70px;height:40px;background:var(--red);border-radius:6px}
.play svg{position:absolute;left:26px;top:11px}
.thumb{position:absolute;top:775px;width:251px;height:235px;background:var(--light)}
.thumb-img{position:absolute;left:0;top:0;width:251px;height:134px}
.thumb h4{position:absolute;left:14px;top:146px;font-size:14px;font-weight:600;color:var(--ink)}
.thumb p{position:absolute;left:14px;top:170px;width:224px;font-size:9px;line-height:13px;color:var(--muted)}
.thumb.dark{background:#1a1a1a}
.thumb.dark h4{color:var(--white)}

/* current projects */
.projects{top:2445px;height:720px}
.tile{position:absolute;width:336px;height:201px}
.tile-caption{position:absolute;left:0;top:0;width:336px;height:201px;background:rgba(0,0,0,.55)}
.tile-caption h4{position:absolute;left:40px;top:110px;color:var(--white);font-size:15px;font-weight:600}
.tile-caption p{position:absolute;left:40px;top:140px;width:260px;color:#ccc;font-size:9px;line-height:13px}

/* other stuff */
.other{top:3165px;height:470px}
.stuff{position:absolute;top:103px;width:250px;height:341px}
.stuff .btn{left:0;top:275px;width:250px;height:54px;line-height:54px;font-size:15px;font-weight:400}

/* blog */
.blog{top:3635px;height:632px}
.post{position:absolute;width:480px;height:166px}
.post-img{position:absolute;left:0;top:0;width:232px;height:166px}
.post h4{position:absolute;left:248px;top:0;color:var(--ink);font-size:16px;font-weight:600}
.post .meta{position:absolute;left:248px;top:26px;font-size:10px;color:var(--muted)}
.post p{position:absolute;left:248px;top:50px;width:230px;font-size:11px;line-height:16px;color:var(--text)}
.post .more{position:absolute;left:248px;top:132px;font-size:11px;color:var(--red);font-weight:600}
.blog-divider{position:absolute;left:598px;top:150px;height:372px;border-left:1px solid #ddd}

/* contact */
.contact{top:4267px;height:433px;background:var(--black)}
.contact .title{color:var(--white);top:54px}
.contact-rule{position:absolute;left:78px;top:112px;width:1044px;border-top:1px solid #333}
.contact-brand{position:absolute;left:100px;top:135px;width:120px;text-align:center}
.contact-brand .brand-mark{width:70px;height:70px;background:#333;margin-bottom:8px}
.contact-brand .brand-name{color:#555;font-size:11px}
.address,.reach{position:absolute;top:140px;color:#777;font-size:12px;line-height:20px;text-transform:uppercase}
.address{left:282px}
.reach{left:545px}
.social{position:absolute;left:934px;top:146px;display:flex;gap:10px}
.social i{display:block;width:42px;height:42px;border-radius:50%;background:#9a9a9a}
.footer-bar{position:absolute;left:78px;top:333px;width:1044px;height:84px;background:var(--red);text-align:center;color:var(--white)}
.footer-nav{margin-top:20px;font-size:12px;word-spacing:2px}
.footer-nav span{margin:0 9px}
.copyright{font-size:11px;margin-top:8px}
</style>
</head>
<body>

<header class="section site-header">
  <div class="brand">
    <div class="brand-mark"></div>
    <div class="brand-name">Copper Lantern Films</div>
  </div>
  <div class="search">Search
    <svg width="20" height="20" viewBox="0 0 20 20"><circle cx="8" cy="8" r="6" fill="none" stroke="#222" stroke-width="2.5"/><line x1="12.5" y1="12.5" x2="18" y2="18" stroke="#222" stroke-width="3"/></svg>
  </div>
  <nav class="main-nav">
    <span class="active">HOME</span><span>ABOUT US</span><span>PORTFOLIO</span><span>CURRENT PROJECTS</span><span>OTHER STUFF</span><span>BLOG</span><span>CONTACT</span>
  </nav>
</header>

<section class="section hero">
  <div class="ph hero-photo" role="img" aria-label="Photo of a cameraman with a camera on a tripod against a bright grey backdrop"></div>
  <div class="hero-kicker">WE ARE SPECIAL IN</div>
  <div class="hero-title">SHORT FILMS &amp;<br>DOCUMENTARY</div>
  <p class="hero-text">Lorem ipsum dolor sit amet, consectetuer adipiscing elit. Aenean commodo ligula eget dolor. Aenean massa. Cum sociis natoque penatibus et magnis dis parturient montes.</p>
  <div class="btn hero-btn">VIEW OUR PORTFOLIO</div>
  <div class="dots" style="left:86px;top:536px"><i class="on"></i><i></i><i></i><i></i><i></i></div>
</section>

<section class="section about">
  <h2 class="title" style="top:64px">ABOUT US</h2>
  <div class="title-rule" style="top:120px"></div>
  <p class="intro" style="top:152px">Donec quam felis, ultricies nec, pellentesque eu, pretium quis, sem. Nulla consequat massa quis enim. Donec pede justo, fringilla vel, aliquet nec, vulputate eget, arcu. In enim justo, rhoncus ut, imperdiet a, venenatis vitae, justo. Nullam dictum felis eu pede mollis pretium. Integer tincidunt. Cras dapibus. Vivamus elementum semper nisi. Aenean vulputate eleifend tellus. Aenean leo ligula, porttitor eu, consequat vitae, eleifend ac, enim. Aliquam lorem ante, dapibus in, viverra quis, feugiat a, tellus. Phasellus viverra nulla ut metus varius laoreet. Quisque rutrum. Aenean varius laoreet.</p>
  <div class="member" style="left:294px">
    <div class="member-photo" role="img" aria-label="Portrait photo of a team member"></div>
    <div class="member-name">JOHN SMITH LB</div>
    <div class="btn">VIEW PROFILE</div>
  </div>
  <div class="member" style="left:501px">
    <div class="member-photo" role="img" aria-label="Portrait photo of a team member" style="background:linear-gradient(180deg,#e8e8e8,#6d5446)"></div>
    <div class="member-name">LADY SMITH LB</div>
    <div class="btn">VIEW PROFILE</div>
  </div>
  <div class="member" style="left:708px">
    <div class="member-photo" role="img" aria-label="Portrait photo of a team member" style="background:linear-gradient(180deg,#4a4a4a,#0e0e0e)"></div>
    <div class="member-name">JOHN SMITH LB</div>
    <div class="btn">VIEW PROFILE</div>
  </div>
</section>

<section class="section portfolio">
  <h2 class="title" style="top:38px">PORTFOLIO</h2>
  <div class="title-rule" style="top:96px"></div>
  <p class="intro" style="top:130px">Donec quam felis, ultricies nec, pellentesque eu, pretium quis, sem. Nulla consequat massa quis enim. Donec pede justo, fringilla vel, aliquet nec, vulputate eget, arcu. In enim justo, rhoncus ut, imperdiet a, venenatis vitae, justo. Nullam dictum felis eu pede mollis pretium. Integer tincidunt. Cras dapibus.</p>
  <div class="ph video" role="img" aria-label="Dark video still of a film projector and a man's face"></div>
  <div class="play"><svg width="18" height="18" viewBox="0 0 18 18"><polygon points="2,1 17,9 2,17" fill="#fff"/></svg></div>

  <div class="thumb dark" style="left:78px">
    <div class="thumb-img" role="img" aria-label="Video thumbnail of a film scene" style="background:linear-gradient(135deg,#555,#1e1e1e)"></div>
    <svg style="position:absolute;left:104px;top:46px" width="44" height="36" viewBox="0 0 44 36"><rect width="44" height="36" rx="5" fill="#ddd"/><polygon points="17,10 30,18 17,26" fill="#555"/></svg>
    <h4>NULLAM DICTUM FELI</h4>
    <p>AENEAN VULPUTATE ELEIFEND TELLUS. AENEAN LEO LIGULA, PORTTITOR EU, CONSEQUAT VITAE, ELEIFEND AC.</p>
  </div>
  <div class="thumb" style="left:345px">
    <div class="thumb-img" role="img" aria-label="Video thumbnail of a woman in a studio" style="background:linear-gradient(135deg,#b89c8a,#5e4a40)"></div>
    <h4>NULLAM DICTUM FELI</h4>
    <p>AENEAN VULPUTATE ELEIFEND TELLUS. AENEAN LEO LIGULA, PORTTITOR EU, CONSEQUAT VITAE, ELEIFEND AC.</p>
  </div>
  <div class="thumb" style="left:608px">
    <div class="thumb-img" role="img" aria-label="Video thumbnail of a woman in a black dress" style="background:linear-gradient(135deg,#e6e6e6,#8a8a8a)"></div>
    <h4>NULLAM DICTUM FELI</h4>
    <p>AENEAN VULPUTATE ELEIFEND TELLUS. AENEAN LEO LIGULA, PORTTITOR EU, CONSEQUAT VITAE, ELEIFEND AC.</p>
  </div>
  <div class="thumb" style="left:871px">
    <div class="thumb-img" role="img" aria-label="Video thumbnail of a film crew at work" style="background:linear-gradient(135deg,#7d8fa3,#2e3640)"></div>
    <h4>NULLAM DICTUM FELI</h4>
    <p>AENEAN VULPUTATE ELEIFEND TELLUS. AENEAN LEO LIGULA, PORTTITOR EU, CONSEQUAT VITAE, ELEIFEND AC.</p>
  </div>
</section>

<section class="section projects">
  <h2 class="title" style="top:84px">CURRENT PROJECTS</h2>
  <div class="title-rule" style="top:142px"></div>
  <div class="tile ph" style="left:78px;top:212px;background:linear-gradient(135deg,#666,#222)" role="img" aria-label="Behind the scenes photo of a film set">
    <div class="tile-caption"><h4>NULLAM DICTUM FELI</h4><p>AENEAN VULPUTATE ELEIFEND TELLUS. AENEAN LEO LIGULA, PORTTITOR EU, CONSEQUAT VITAE.</p></div>
  </div>
  <div class="tile ph" style="left:432px;top:212px;background:linear-gradient(135deg,#c9d6de,#6f8694)" role="img" aria-label="Photo of an actress seated in a director's chair"></div>
  <div class="tile ph" style="left:786px;top:212px;background:linear-gradient(135deg,#f2b233,#7a3a08)" role="img" aria-label="Photo of a camera crew against a sunset"></div>
  <div class="tile ph" style="left:78px;top:431px;background:linear-gradient(135deg,#c8c2b8,#6b6358)" role="img" aria-label="Photo of a film crew shooting on a street"></div>
  <div class="tile ph" style="left:432px;top:431px;background:linear-gradient(135deg,#444,#0d0d0d)" role="img" aria-label="Photo of a camera operator in a dark studio"></div>
  <div class="tile ph" style="left:786px;top:431px;background:linear-gradient(180deg,#8a9aa6,#2a2f33)" role="img" aria-label="Photo of camera operators against a cloudy sky"></div>
</section>

<section class="section other">
  <h2 class="title" style="top:0">OTHER STUFF</h2>
  <div class="title-rule" style="top:58px"></div>
  <div class="stuff ph" style="left:78px;background:linear-gradient(135deg,#d9a04a,#7b4a22)" role="img" aria-label="Photo of a photographer holding a camera">
    <div class="btn">PHOTOGRAPHY</div>
  </div>
  <div class="stuff ph" style="left:342px;background:linear-gradient(135deg,#8a4b2c,#3a1d10)" role="img" aria-label="Photo of old books stacked on a shelf">
    <div class="btn">POETRY</div>
  </div>
  <div class="stuff ph" style="left:606px;background:linear-gradient(135deg,#8fcac4,#3f8a86)" role="img" aria-label="Photo of a vintage studio microphone">
    <div class="btn">AUDIO</div>
  </div>
  <div class="stuff ph" style="left:871px;background:linear-gradient(135deg,#e8e8e8,#a8b0b8)" role="img" aria-label="Photo of a designer working with a graphics tablet">
    <div class="btn">ANIMATION &amp; VFX</div>
  </div>
</section>

<section class="section blog">
  <h2 class="title" style="top:60px">OUR BLOG</h2>
  <div class="title-rule" style="top:118px"></div>
  <div class="blog-divider"></div>

  <article class="post" style="left:78px;top:155px">
    <div class="post-img ph" role="img" aria-label="Photo of film reels" style="background:linear-gradient(135deg,#bbb,#333)"></div>
    <h4>DONEC QUAM FELISNEC</h4>
    <div class="meta">Posted by John on 28 Nov 2014</div>
    <p>Aenean vulputate eleifend tellus. Aenean leo ligula, porttitor eu, consequat vitae, eleifend ac, enim. Aliquam lorem ante, dapibus in, viverra nulla ut metus.</p>
    <div class="more">READ MORE</div>
  </article>
  <article class="post" style="left:636px;top:155px">
    <div class="post-img ph" role="img" aria-label="Photo of a cameraman with a tripod" style="background:linear-gradient(135deg,#ddd,#555)"></div>
    <h4>DONEC QUAM FELISNEC</h4>
    <div class="meta">Posted by John on 28 Nov 2014</div>
    <p>Aenean vulputate eleifend tellus. Aenean leo ligula, porttitor eu, consequat vitae, eleifend ac, enim. Aliquam lorem ante, dapibus in, viverra nulla ut metus.</p>
    <div class="more">READ MORE</div>
  </article>
  <article class="post" style="left:78px;top:350px">
    <div class="post-img ph" role="img" aria-label="Photo of a figure with raised arms against a sunset" style="background:linear-gradient(135deg,#f5b429,#b34b0a)"></div>
    <h4>DONEC QUAM FELISNEC</h4>
    <div class="meta">Posted by John on 28 Nov 2014</div>
    <p>Aenean vulputate eleifend tellus. Aenean leo ligula, porttitor eu, consequat vitae, eleifend ac, enim. Aliquam lorem ante, dapibus in, viverra nulla ut metus.</p>
    <div class="more">READ MORE</div>
  </article>
  <article class="post" style="left:636px;top:350px">
    <div class="post-img ph" role="img" aria-label="Photo of a vintage film projector" style="background:linear-gradient(135deg,#8aa0b4,#2c3844)"></div>
    <h4>DONEC QUAM FELISNEC</h4>
    <div class="meta">Posted by John on 28 Nov 2014</div>
    <p>Aenean vulputate eleifend tellus. Aenean leo ligula, porttitor eu, consequat vitae, eleifend ac, enim. Aliquam lorem ante, dapibus in, viverra nulla ut metus.</p>
    <div class="more">READ MORE</div>
  </article>

  <div class="dots" style="left:556px;top:570px">
    <i style="border:none;background:var(--red)"></i><i style="border:none;background:#555"></i><i style="border:none;background:#555"></i><i style="border:none;background:#555"></i>
  </div>
</section>

<footer class="section contact">
  <h2 class="title">CONTACT US</h2>
  <div class="contact-rule"></div>
  <div class="contact-brand">
    <div class="brand-mark"></div>
    <div class="brand-name">Copper Lantern Films</div>
  </div>
  <div class="address">Donec sodales sagittis magna,<br>sed consequat, leo eget,<br>bibendum sodales,<br>augue velit cursus nunc.</div>
  <div class="reach">Phone: 044 7120 58342<br>Email: info@copperlanternfilms.com</div>
  <div class="social"><i></i><i></i><i></i><i></i></div>
  <div class="footer-bar">
    <div class="footer-nav"><span>HOME</span><span>ABOUT US</span><span>PORTFOLIO</span><span>CURRENT PROJECTS</span><span>OTHER STUFF</span><span>BLOG</span><span>CONTACT</span></div>
    <div class="copyright">ALL RIGHTS RESERVED. COPYRIGHTS @ 2014</div>
  </div>
</footer>

</body>
</html>
```